Stylish Business Cards Wanted

- DOUBLE SIDED Design Required -

High end, edgy cards for a corporate and personal stylist. Must include logo,
Name: Belinda Harwick
Title: Director and Stylist
telephone : +61 8 7142 5809
email: belinda@theloombriefing.example
website: theloombriefing.example
Tag: Corporate Workwear & Uniform Specialist | Personal Stylist
Would like nice icons for telephone, email, website

Target Market(s)

Businesses wanting stylish uniforms, people wanting stylish wardrobes

Industry/Entity Type

Corporate Workwear Stylist

Contact Information for Business Card

I would like black, white and gold foiling incorporated in the design - possibly a touch of the other colours on my branding guide attached Name: Belinda Harwick Title: Director and Stylist telephone : +61 8 7142 5809 email: belinda@theloombriefing.example website: theloombriefing.example Tag: Corporate Workwear & Uniform Specialist | Personal Stylist Would like nice icons for telephone, email, website

Font styles to use
Other font styles liked:
• Raleway

Colors

Designer to choose colors to be used in the design.

Requirements
Must have
• Gold foil accents

```html
<!DOCTYPE html>
<html lang="en">
<head>
<meta charset="utf-8">
<title>The Loom Briefing — Business Cards</title>
<link rel="stylesheet" href="https://fonts.googleapis.com/css2?family=Open+Sans:wght@400;600;700&display=swap">
<style>
  :root {
    --backdrop: #2a2a2c;
    --card: #141415;
    --gold: #c8b878;
    --gold-soft: #a89a62;
    --shadow: rgba(0, 0, 0, 0.55);
  }
  * { box-sizing: border-box; margin: 0; padding: 0; }
  html, body {
    width: 1200px;
    height: 900px;
    overflow: hidden;
    background: var(--backdrop);
    font-family: "Open Sans", Arial, sans-serif;
  }
  .canvas {
    width: 1200px;
    height: 900px;
    display: flex;
    flex-direction: column;
    align-items: center;
    justify-content: center;
    gap: 40px;
  }
  .card {
    position: relative;
    width: 700px;
    height: 400px;
    background: var(--card);
    box-shadow: 0 18px 40px var(--shadow);
    color: var(--gold);
  }

  /* Front */
  .card--front .brand-name {
    position: absolute;
    top: 120px;
    left: 0;
    right: 0;
    text-align: center;
    font-size: 56px;
    font-weight: 600;
    letter-spacing: 0.5px;
    color: var(--gold);
  }
  .card--front .tagline {
    position: absolute;
    right: 44px;
    bottom: 40px;
    font-size: 17px;
    color: var(--gold-soft);
    letter-spacing: 0.3px;
  }
  .tagline .dot { margin: 0 10px; }

  /* Back */
  .card--back .brand-name {
    position: absolute;
    top: 56px;
    right: 44px;
    font-size: 32px;
    font-weight: 600;
    color: var(--gold);
  }
  .card--back .contact-block {
    position: absolute;
    left: 56px;
    bottom: 48px;
  }
  .person-name {
    font-size: 22px;
    font-weight: 700;
    letter-spacing: 1px;
    text-transform: uppercase;
    color: var(--gold);
  }
  .person-title {
    font-size: 16px;
    color: var(--gold-soft);
    margin-bottom: 22px;
  }
  .contact-list { list-style: none; }
  .contact-item {
    display: flex;
    align-items: center;
    gap: 10px;
    font-size: 17px;
    color: var(--gold-soft);
    line-height: 1.55;
  }
  .contact-icon { width: 15px; height: 15px; flex: none; }
</style>
</head>
<body>
<main class="canvas">
  <section class="card card--front" aria-label="Card front">
    <div class="brand-name">The Loom Briefing</div>
    <p class="tagline">Corporate Workwear &amp; Uniform Specialist<span class="dot">•</span>Personal Stylist</p>
  </section>

  <section class="card card--back" aria-label="Card back">
    <div class="brand-name">The Loom Briefing</div>
    <div class="contact-block">
      <p class="person-name">Belinda Harwick</p>
      <p class="person-title">Director and Stylist</p>
      <ul class="contact-list">
        <li class="contact-item">
          <svg class="contact-icon" viewBox="0 0 16 16" aria-hidden="true">
            <path fill="#c8b878" d="M3.6 1.2l2.3 2.6-1.2 1.6c.9 2 2.4 3.5 4.3 4.4l1.6-1.2 2.6 2.3-1.3 2.2C7.2 13.3 2.7 8.8 1.6 3.1z"/>
          </svg>
          +61 8 7142 5809
        </li>
        <li class="contact-item">
          <svg class="contact-icon" viewBox="0 0 16 16" aria-hidden="true">
            <rect x="1" y="3.5" width="14" height="9" rx="1" fill="#c8b878"/>
            <path d="M1.5 4.2L8 9l6.5-4.8" fill="none" stroke="#141415" stroke-width="1.2"/>
          </svg>
          belinda@theloombriefing.example
        </li>
        <li class="contact-item">
          <svg class="contact-icon" viewBox="0 0 16 16" aria-hidden="true">
            <circle cx="8" cy="8" r="6.5" fill="none" stroke="#c8b878" stroke-width="1.4"/>
            <ellipse cx="8" cy="8" rx="2.8" ry="6.5" fill="none" stroke="#c8b878" stroke-width="1.1"/>
            <path d="M1.5 8h13" stroke="#c8b878" stroke-width="1.1"/>
          </svg>
          theloombriefing.example
        </li>
      </ul>
    </div>
  </section>
</main>
</body>
</html>
```